Stationery Design Project

Please create a custom Stationery Design for Pinecrest Dwellings. The logo is attached to this brief.

Please Include:
- Letterhead
- With Compliments slip
- Envelope

Please also see open Business Card project: http://briefs.sketchvault.example/task.aspx?id=517290

Industry/Entity Type

Business

```html
<!DOCTYPE html>
<html lang="en">
<head>
<meta charset="utf-8">
<title>Pinecrest Dwellings – Stationery</title>
<link rel="stylesheet" href="https://fonts.googleapis.com/css2?family=Open+Sans:wght@400;600&display=swap">
<style>
  :root {
    --stage: #5e5e5e;
    --paper: #ffffff;
    --brand-blue: #0a72bd;
    --brand-green: #8cc63f;
    --text-grey: #5a5a5a;
    --mark-grey: #e2e2e2;
    --rule-grey: #b9b9b9;
  }
  * { box-sizing: border-box; margin: 0; padding: 0; }
  html, body { width: 1200px; height: 640px; overflow: hidden; }
  body {
    position: relative;
    background: var(--stage);
    font-family: "Open Sans", Arial, sans-serif;
    color: var(--text-grey);
  }
  .sheet {
    position: absolute;
    background: var(--paper);
    box-shadow: 2px 3px 6px rgba(0,0,0,.35);
    overflow: hidden;
  }
  .sheet__wave { position: absolute; left: 0; top: 0; width: 100%; display: block; }
  .sheet__base { position: absolute; left: 0; bottom: 0; width: 100%; }
  .sheet__base-green { height: 2px; background: var(--brand-green); margin-bottom: 2px; }
  .sheet__base-blue { height: 6px; background: var(--brand-blue); }

  .brand-name {
    font-weight: 600;
    color: var(--brand-blue);
    line-height: 1.1;
    display: flex;
    align-items: center;
    gap: 6px;
  }
  .brand-name__dot {
    width: 10px; height: 10px; border-radius: 50%;
    background: var(--brand-green); flex: none;
  }
  .faint-mark {
    position: absolute;
    font-weight: 600;
    color: var(--mark-grey);
    text-align: center;
    line-height: 1.05;
  }
  .contact { font-size: 5.5px; line-height: 1.5; color: var(--text-grey); }
  .contact-row { display: flex; align-items: center; gap: 3px; }
  .contact-icon { width: 6px; height: 6px; flex: none; }
  .divider { width: 1px; background: var(--rule-grey); align-self: stretch; }

  /* Letterhead */
  .letterhead { left: 70px; top: 56px; width: 400px; height: 536px; }
  .letterhead .brand-name { position: absolute; right: 34px; top: 88px; font-size: 15px; }
  .letterhead .faint-mark { left: 90px; top: 250px; width: 190px; font-size: 30px; }
  .letterhead__footer {
    position: absolute; left: 0; right: 0; bottom: 22px;
    text-align: center;
  }
  .letterhead__footer .contact-row { justify-content: center; gap: 10px; }
  .letterhead__footer .contact-row span { display: flex; align-items: center; gap: 3px; }

  /* Envelope front */
  .envelope-front { left: 530px; top: 24px; width: 448px; height: 178px; }
  .envelope-front .faint-mark { right: 26px; top: 64px; width: 110px; font-size: 18px; }
  .envelope-front__sender {
    position: absolute; left: 30px; bottom: 20px;
    display: flex; gap: 8px; align-items: center;
  }
  .envelope-front .brand-name { font-size: 12px; }

  /* Envelope back */
  .envelope-back { left: 724px; top: 230px; width: 446px; height: 178px; }
  .envelope-back__flap { position: absolute; left: 0; top: 0; width: 100%; height: 50px; }
  .envelope-back .brand-name { position: absolute; left: 50%; top: 14px; transform: translateX(-50%); font-size: 10px; white-space: nowrap; }

  /* Compliments slip */
  .compliments { left: 558px; top: 438px; width: 364px; height: 160px; }
  .compliments__title {
    position: absolute; right: 28px; top: 38px;
    font-size: 11.5px; color: var(--brand-blue); font-weight: 400;
  }
  .compliments__sender {
    position: absolute; left: 24px; bottom: 18px;
    display: flex; gap: 6px; align-items: center;
  }
  .compliments .brand-name { font-size: 10px; }
</style>
</head>
<body>

  <!-- Letterhead -->
  <section class="sheet letterhead" aria-label="Letterhead">
    <svg class="sheet__wave" viewBox="0 0 400 110" preserveAspectRatio="none" height="110" aria-hidden="true">
      <path d="M0 0 H400 V62 C380 40 350 22 300 22 C200 24 110 54 0 58 Z" fill="var(--brand-blue)"/>
      <path d="M0 64 C120 64 220 30 300 24 C230 36 140 72 0 74 Z" fill="var(--brand-green)"/>
    </svg>
    <div class="brand-name"><span class="brand-name__dot"></span>Pinecrest Dwellings</div>
    <div class="faint-mark">Pinecrest Dwellings</div>
    <div class="letterhead__footer contact">
      <div class="contact-row">
        <span>
          <svg class="contact-icon" viewBox="0 0 10 10" aria-hidden="true"><rect width="10" height="10" rx="2" fill="var(--brand-blue)"/><path d="M3 2.5 L4.2 2.5 L4.6 4 L3.9 4.6 C4.3 5.4 4.7 5.8 5.4 6.1 L6 5.4 L7.5 5.8 L7.5 7 C5 7.3 2.7 5 3 2.5Z" fill="#fff"/></svg>
          020 7946 0321
        </span>
        <span>
          <svg class="contact-icon" viewBox="0 0 10 10" aria-hidden="true"><rect width="10" height="10" rx="2" fill="var(--brand-blue)"/><circle cx="5" cy="5" r="2.6" fill="none" stroke="#fff" stroke-width="0.9"/><path d="M2.4 5 H7.6" stroke="#fff" stroke-width="0.8"/></svg>
          www.pinecrestdwellings.example
        </span>
      </div>
      <div>12 Alder Court, Address Line, Millbrook Business Park, City Name</div>
    </div>
    <div class="sheet__base"><div class="sheet__base-green"></div><div class="sheet__base-blue"></div></div>
  </section>

  <!-- Envelope front -->
  <section class="sheet envelope-front" aria-label="Envelope front">
    <svg class="sheet__wave" viewBox="0 0 448 70" preserveAspectRatio="none" height="70" aria-hidden="true">
      <path d="M0 0 H448 V52 C430 34 400 20 360 20 C260 22 140 40 0 42 Z" fill="var(--brand-blue)"/>
      <path d="M0 48 C140 48 260 26 360 20 C270 34 150 58 0 58 Z" fill="var(--brand-green)"/>
    </svg>
    <div class="faint-mark">Pinecrest Dwellings</div>
    <div class="envelope-front__sender">
      <div class="brand-name"><span class="brand-name__dot"></span>Pinecrest Dwellings</div>
      <div class="divider"></div>
      <div class="contact">12 Alder Court, Address Line<br>Millbrook Business Park, City Name</div>
    </div>
    <div class="sheet__base"><div class="sheet__base-green"></div><div class="sheet__base-blue"></div></div>
  </section>

  <!-- Envelope back -->
  <section class="sheet envelope-back" aria-label="Envelope back">
    <svg class="envelope-back__flap" viewBox="0 0 446 50" preserveAspectRatio="none" aria-hidden="true">
      <path d="M0 6 C12 6 16 12 22 26 C28 42 36 48 60 48 H386 C410 48 418 42 424 26 C430 12 434 6 446 6" fill="none" stroke="var(--rule-grey)" stroke-width="1"/>
    </svg>
    <div class="brand-name"><span class="brand-name__dot"></span>Pinecrest Dwellings</div>
  </section>

  <!-- With Compliments slip -->
  <section class="sheet compliments" aria-label="With compliments slip">
    <svg class="sheet__wave" viewBox="0 0 364 70" preserveAspectRatio="none" height="70" aria-hidden="true">
      <path d="M0 0 H364 V50 C350 32 320 18 290 18 C200 20 110 40 0 42 Z" fill="var(--brand-blue)"/>
      <path d="M0 48 C110 48 210 26 300 18 C220 32 120 58 0 58 Z" fill="var(--brand-green)"/>
    </svg>
    <div class="compliments__title">With Compliments</div>
    <div class="compliments__sender">
      <div class="brand-name"><span class="brand-name__dot"></span>Pinecrest Dwellings</div>
      <div class="divider"></div>
      <div class="contact">12 Alder Court, Address Line<br>Millbrook Business Park, City Name</div>
      <div class="divider"></div>
      <div class="contact">
        <div class="contact-row">
          <svg class="contact-icon" viewBox="0 0 10 10" aria-hidden="true"><rect width="10" height="10" rx="2" fill="var(--brand-blue)"/><path d="M3 2.5 L4.2 2.5 L4.6 4 L3.9 4.6 C4.3 5.4 4.7 5.8 5.4 6.1 L6 5.4 L7.5 5.8 L7.5 7 C5 7.3 2.7 5 3 2.5Z" fill="#fff"/></svg>
          020 7946 0321
        </div>
        <div class="contact-row">
          <svg class="contact-icon" viewBox="0 0 10 10" aria-hidden="true"><rect width="10" height="10" rx="2" fill="var(--brand-blue)"/><circle cx="5" cy="5" r="2.6" fill="none" stroke="#fff" stroke-width="0.9"/><path d="M2.4 5 H7.6" stroke="#fff" stroke-width="0.8"/></svg>
          www.pinecrestdwellings.example
        </div>
      </div>
    </div>
    <div class="sheet__base"><div class="sheet__base-green"></div><div class="sheet__base-blue"></div></div>
  </section>

</body>
</html>
```